Blind Rivet Product catalogue

Need a design in wordpress with a productcatalogue where i present all products. This is a B2B business. The products is Blindrivets and Blindrivet nuts and accessories to this. I only want the basic information and also technical specification.

This is a subcompany to my existing company k7.m3.se but specializing in a subcategory

Businesses using blind rivet technology.

Industrial

Sans Serif

Must have
• Three different categories for the products; Blind Rivets - Blind Rivet Nut - Riveting Tools
Nice to have
• Possible to ad login for more information of the different sizes

```html
<!DOCTYPE html>
<html lang="en">
<head>
<meta charset="utf-8">
<title>K7M3 – Blind Rivet Catalogue</title>
<link href="https://fonts.googleapis.com/css2?family=Montserrat:wght@400;500;600;700&display=swap" rel="stylesheet">
<style>
:root{
  --black:#000;
  --white:#fff;
  --green:#5cb83c;
  --red:#e8001e;
  --red-soft:#f5283c;
  --ink:#222;
  --card-bg:#f7f8fc;
  --card-img:#e4e4e4;
}
*{margin:0;padding:0;box-sizing:border-box}
html,body{width:1200px;height:2782px;overflow:hidden}
body{position:relative;font-family:'Montserrat',sans-serif;color:var(--ink);background:var(--white)}
.abs{position:absolute}
a{color:inherit;text-decoration:none}

/* header */
.site-header{left:0;top:0;width:1200px;height:143px;background:var(--black)}
.brand{left:106px;top:42px;display:flex;flex-direction:column;align-items:flex-start;color:var(--white)}
.brand-row{display:flex;align-items:center;gap:7px}
.brand-mark{width:14px;height:14px;background:var(--green)}
.brand-name{font-size:26px;font-weight:600;letter-spacing:1px;line-height:1}
.brand-tag{font-size:9px;font-weight:400;color:#aaa;margin-top:5px}
.account{top:24px;font-size:13px;font-weight:700;color:var(--white);line-height:18px}
.account.login{left:892px;color:var(--red)}
.account.sep{left:952px}
.account.register{left:977px}
.account.cart{left:1084px;display:flex;align-items:center;gap:6px}
.main-nav{top:88px;font-size:18px;font-weight:700;color:var(--white);line-height:22px}
.nav-underline{left:542px;top:138px;width:74px;height:5px;background:var(--green)}

/* hero */
.hero{left:0;top:143px;width:1200px;height:628px;background:linear-gradient(120deg,#6a4a38 0%,#4e3a34 45%,#3f3440 70%,#5a4d48 100%)}
.hero-title{left:0;top:386px;width:1200px;text-align:center;font-size:45px;font-weight:700;color:var(--white);line-height:52px}
.btn{display:flex;align-items:center;justify-content:center;font-weight:700;color:var(--white);background:var(--green);text-transform:uppercase}
.hero-btn{left:532px;top:503px;width:136px;height:41px;font-size:13px}
.dot{top:670px;width:16px;height:16px;border-radius:50%;background:var(--white)}
.dot.active{background:var(--green)}

/* welcome */
.welcome-accent{left:93px;top:831px;width:448px;height:333px;background:linear-gradient(90deg,var(--red-soft),var(--red))}
.welcome-photo{left:138px;top:867px;width:450px;height:333px;background:linear-gradient(160deg,#f2f2f2 0%,#d9d9d9 35%,#6a6a6a 55%,#c9c2a8 80%,#eeeeee 100%)}
.welcome-title{left:642px;top:836px;font-size:46px;font-weight:700;color:var(--black);line-height:58px}
.welcome-text{left:639px;top:907px;width:432px;font-size:13px;font-weight:400;line-height:22.2px;color:var(--ink)}
.welcome-btn{left:639px;top:1149px;width:136px;height:42px;font-size:13px}

/* products */
.section-title{left:0;width:1200px;text-align:center;font-weight:700;color:var(--black)}
.products-title{top:1325px;font-size:33px;line-height:40px}
.product-card{top:1404px;width:331px;height:456px;background:var(--card-bg);box-shadow:0 1px 6px rgba(0,0,0,.18)}
.product-image{width:100%;height:264px;background:var(--card-img)}
.product-image.rivet{background:linear-gradient(170deg,#e4e4e4 0%,#e4e4e4 38%,#c9c9c9 48%,#b5b5b5 52%,#e4e4e4 62%,#e4e4e4 100%)}
.product-image.nut{background:radial-gradient(ellipse 90px 80px at 50% 50%,#b9b9b9 0%,#d2d2d2 55%,#e4e4e4 100%)}
.product-image.tool{background:radial-gradient(ellipse 70px 100px at 48% 50%,#3a3a3a 0%,#8a8a8a 55%,#e4e4e4 100%)}
.product-name{margin-top:26px;text-align:center;font-size:23px;font-weight:600;line-height:30px;color:var(--ink)}
.product-price{margin-top:14px;text-align:center;font-size:23px;font-weight:600;line-height:30px;color:var(--ink)}
.product-btn{margin:18px auto 0;width:201px;height:46px;font-size:16px;border-radius:4px}

/* promo band */
.promo{left:0;top:1988px;width:1200px;height:141px;background:var(--red)}
.promo-text{left:145px;top:2045px;font-size:21.5px;font-weight:700;color:var(--white);line-height:26px}
.promo-btn{left:919px;top:2032px;width:159px;height:52px;background:var(--black);color:var(--white);font-size:17px;font-weight:700;display:flex;align-items:center;justify-content:center}

/* clients */
.clients-title{top:2153px;font-size:34px;line-height:42px}
.client-card{top:2225px;width:230px;height:210px;background:var(--white);box-shadow:0 0 10px rgba(0,0,0,.08);display:flex;align-items:center;justify-content:center;gap:8px;font-size:22px;font-weight:700;color:var(--black)}
.client-mark{width:14px;height:14px;background:var(--black)}

/* footer */
.site-footer{left:0;top:2509px;width:1200px;height:273px;background:var(--black)}
.footer-brand{left:111px;top:2600px}
.footer-brand .brand-name{font-size:34px}
.footer-brand .brand-mark{width:18px;height:18px}
.footer-brand .brand-tag{font-size:12px}
.footer-nav{top:2583px;font-size:18px;font-weight:700;color:var(--white);line-height:22px}
.social{top:2641px;width:44px;height:44px;border-radius:50%;border:2px solid #fff;display:flex;align-items:center;justify-content:center;font-size:10px;font-weight:700;color:var(--white)}
.copyright{left:866px;top:2715px;font-size:13px;color:var(--white);line-height:18px}
.to-top{left:1117px;top:2707px;width:40px;height:40px;border-radius:50%;background:#555;border:3px solid #333;display:flex;align-items:center;justify-content:center}
</style>
</head>
<body>

<header class="abs site-header"></header>
<div class="abs brand">
  <div class="brand-row"><span class="brand-mark"></span><span class="brand-name">K7M3</span></div>
  <span class="brand-tag">Rostfria lösningar</span>
</div>
<a class="abs account login">Login</a>
<span class="abs account sep">|</span>
<a class="abs account register">Register</a>
<a class="abs account cart">
  <svg width="16" height="14" viewBox="0 0 16 14" aria-hidden="true"><path d="M0 1h3l2 8h9l2-6H4.5" fill="none" stroke="#fff" stroke-width="2"/><circle cx="6" cy="12" r="1.6" fill="#fff"/><circle cx="13" cy="12" r="1.6" fill="#fff"/></svg>(0)
</a>
<a class="abs main-nav" style="left:550px">Home</a>
<a class="abs main-nav" style="left:650px">About Us</a>
<a class="abs main-nav" style="left:780px">Products</a>
<a class="abs main-nav" style="left:907px">Contact Us</a>
<a class="abs main-nav" style="left:1053px">Sitemap</a>
<div class="abs nav-underline"></div>

<section class="abs hero" role="img" aria-label="Photo of rivet pliers and eyelets on leather over a wooden workbench"></section>
<h1 class="abs hero-title">We have everything in<br>stainless A2!</h1>
<a class="abs btn hero-btn">Learn more</a>
<span class="abs dot" style="left:535px"></span>
<span class="abs dot active" style="left:573px"></span>
<span class="abs dot" style="left:611px"></span>
<span class="abs dot" style="left:649px"></span>

<div class="abs welcome-accent"></div>
<div class="abs welcome-photo" role="img" aria-label="Photo of a hand riveter with a ring of blind rivets"></div>
<h2 class="abs welcome-title">Welcome to K7M3</h2>
<p class="abs welcome-text">K7M3 sells stainless steel fasteners to stores, retailers and industry. On our site you can find most known DIN and ISO standards in mounting. We also have a large range of Marine products in stainless steel. Welcome to look around our store. You navigate through the menu at the top of the page, if you want to see an overview of all products in a certain category, click on the name. For example, if you move your mouse over screws in the menu and click on wooden screws, all products in that category are displayed. Each item has a packaging size that is also the smallest order item!</p>
<a class="abs btn welcome-btn">Read more</a>

<h2 class="abs section-title products-title">Products</h2>
<article class="abs product-card" style="left:75px">
  <div class="product-image rivet" role="img" aria-label="Product photo of a stainless blind rivet"></div>
  <h3 class="product-name">Blind Rivets</h3>
  <p class="product-price">24.25 kr</p>
  <a class="btn product-btn">View more</a>
</article>
<article class="abs product-card" style="left:435px">
  <div class="product-image nut" role="img" aria-label="Product photo of a knurled blind rivet nut"></div>
  <h3 class="product-name">Blind Rivet Nut</h3>
  <p class="product-price">24.25 kr</p>
  <a class="btn product-btn">View more</a>
</article>
<article class="abs product-card" style="left:794px">
  <div class="product-image tool" role="img" aria-label="Product photo of a cordless riveting tool"></div>
  <h3 class="product-name">Riveting Tools</h3>
  <p class="product-price">24.25 kr</p>
  <a class="btn product-btn">View more</a>
</article>

<section class="abs promo"></section>
<p class="abs promo-text">NEQUE PORRO QUISQUAM EST QUI DOLOREM IPSUM QUIA</p>
<a class="abs promo-btn">VIEW MORE</a>

<h2 class="abs section-title clients-title">Clients</h2>
<div class="abs client-card" style="left:79px"><span class="client-mark"></span>Vantor</div>
<div class="abs client-card" style="left:353px">Norvolt Energy</div>
<div class="abs client-card" style="left:626px"><span class="client-mark"></span>Bancora</div>
<div class="abs client-card" style="left:900px">Solace Resorts</div>

<footer class="abs site-footer"></footer>
<div class="abs brand footer-brand">
  <div class="brand-row"><span class="brand-mark"></span><span class="brand-name">K7M3</span></div>
  <span class="brand-tag">Rostfria lösningar</span>
</div>
<a class="abs footer-nav" style="left:512px">Home</a>
<a class="abs footer-nav" style="left:611px">About Us</a>
<a class="abs footer-nav" style="left:741px">Products</a>
<a class="abs footer-nav" style="left:869px">Contact Us</a>
<a class="abs footer-nav" style="left:1015px">Sitemap</a>
<a class="abs social" style="left:860px;background:#0b4fa3">Kivo</a>
<a class="abs social" style="left:908px;background:#1d9bf0">Talu</a>
<a class="abs social" style="left:956px;background:#1470b8">Lumo</a>
<a class="abs social" style="left:1005px;background:#d4121c">Rexa</a>
<a class="abs social" style="left:1053px;background:#e4176e">Osta</a>
<p class="abs copyright">© 2020 | www.companyname.com</p>
<a class="abs to-top"><svg width="12" height="8" viewBox="0 0 12 8" aria-hidden="true"><path d="M1 7l5-5 5 5" fill="none" stroke="#fff" stroke-width="2"/></svg></a>

</body>
</html>
```